Website Design for a Chemical Sales Company

We are working with a Chemical Sales Company in California. They sell various chemicals throughout the US.
Types of products they sell: https://www.wardenvale.example/us/products/all
https://www.molvista.example/products/kerrin/glacyn-glycol-thermal-fluids/glacyn-propylene-glycol-thermal-fluids
Some sites to use for inspiration:
https://www.molvista.example
https://www.kerrin.example/en-us
Thank you for taking the time to consider designing a website for us. We are web developers based in Stockton, CA, USA. Most of our projects go through the same process. Understanding this process may help you win a project with us. We custom-code all of our websites in-house. We don’t have any requirements as to what tools you use for your design, but we ask that you follow these guidelines.
IMAGES:
If you use any images or icons in the design, we ask that you have a link to the asset so we can purchase the image/icon. Most of the designs we submit do not have the customer’s images on them unless they have some great images. Be creative; show us the feeling you are trying to portray with your image choices. Use any royalty-free site you choose. We subscribe to Pelmora and mainly use their images, but we can purchase images outside of Pelmora. PLEASE NOTE: we will not submit designs to clients with watermarks on the images.
FONTS:
We ask that you identify the fonts you’re using in the design. This can be done in a message if you want. We typically use Google Fonts and Pelmora Fonts.
CONTENT:
We're always open to different content and ideas. We often submit designs with stock images so the client can see our vision. We typically take pictures after the website launch to use their images with our vision. Lorem Ipsum is fine for paragraphs, but we ask that you make the Headers with correct English. We want to be able to show the vision and identify the sections of the website.
INSPIRATION:
We typically add a couple of links in the brief of websites we like to help you get started in your design.
REVISIONS:
We do not often ask for revisions of the designs unless we see something in the design that may not appeal to the client. If there are slight changes that we want to make, we do that in the development process.
FEEDBACK:
We rarely give feedback on designs during the design process. We are working on many website projects and do not have the time to provide feedback. We usually respond if your request is well thought out and asks specific questions, but a note asking “feedback, please” usually goes unanswered.

```html
<!DOCTYPE html>
<html lang="en">
<head>
<meta charset="utf-8">
<title>Orbilink — Chemical Sales</title>
<link href="https://fonts.googleapis.com/css2?family=Nunito:wght@300;400;600&family=Open+Sans:wght@400;600;700&family=Montserrat:wght@400;500&display=swap" rel="stylesheet">
<style>
:root{
  --blue:#0a8ad9;
  --blue-dark:#0576bd;
  --ink:#1f1f1f;
  --text:#555;
  --light:#f1f1f1;
  --card:#efefef;
  --navy:#0b1a2e;
  --footer:#0c0c0c;
  --white:#fff;
}
*{box-sizing:border-box;margin:0;padding:0}
html,body{width:1200px;height:3734px;overflow:hidden}
body{position:relative;background:var(--white);font-family:"Open Sans",sans-serif;color:var(--ink)}
.center{left:0;width:1200px;text-align:center}

/* header */
.site-header{position:absolute;top:0;left:0;width:1200px;height:109px;background:var(--white);border-top:4px solid var(--blue)}
.logo{position:absolute;left:112px;top:42px;font-family:"Nunito",sans-serif;font-weight:300;font-size:27px;letter-spacing:1px;color:#2a3340;display:flex;align-items:center;gap:8px}
.logo .dot{width:12px;height:12px;border-radius:50%;background:var(--blue)}
.call-badge{position:absolute;left:733px;top:-4px;width:355px;height:52px;background:var(--blue);border-radius:0 0 26px 26px;color:var(--white);font-size:14px;font-weight:600;display:flex;align-items:center;justify-content:center;gap:8px}
.call-badge b{font-size:18px}
.main-nav{position:absolute;top:68px;left:632px;font-size:14px;font-weight:600;color:#222}
.main-nav a{position:absolute;white-space:nowrap;text-decoration:none;color:inherit}
.main-nav .active::after{content:"";position:absolute;left:0;right:0;top:36px;height:3px;background:var(--blue)}

/* hero */
.hero{position:absolute;top:109px;left:0;width:1200px;height:600px;background:radial-gradient(ellipse at 30% 80%,#1f7fd0 0%,transparent 45%),radial-gradient(ellipse at 75% 80%,#8a2e9c 0%,transparent 40%),linear-gradient(180deg,#3b3a4a 0%,#1d3550 45%,#0b2a5a 75%,#0a1a35 100%)}
.hero-panel{position:absolute;left:272px;top:191px;width:655px;height:229px;background:rgba(15,15,20,.72);border-radius:110px 110px 0 0}
.hero-title{position:absolute;top:195px;font-family:"Nunito",sans-serif;font-weight:300;font-size:68px;color:var(--white);letter-spacing:1px}
.hero-text{position:absolute;top:287px;font-family:"Montserrat",sans-serif;font-size:14.5px;line-height:22px;color:var(--white)}
.btn{display:inline-flex;align-items:center;justify-content:center;gap:8px;border-radius:20px;font-weight:700;font-size:14px;color:var(--white);background:var(--blue)}
.hero .btn{position:absolute;left:524px;top:358px;width:151px;height:34px}
.hero-arrow{position:absolute;top:253px;width:44px;height:44px;border-radius:50%;background:rgba(255,255,255,.55);display:flex;align-items:center;justify-content:center}
.hero-dots{position:absolute;top:514px;left:573px;display:flex;gap:8px}
.hero-dots span{width:13px;height:13px;border-radius:50%;border:2px solid var(--white)}
.hero-dots .on{background:var(--white)}

/* featured strip */
.featured{position:absolute;top:709px;left:0;width:1200px;height:371px;background:var(--light)}
.feat-item{position:absolute;top:0;width:240px;text-align:center}
.feat-thumb{margin:40px auto 0;width:140px;height:140px;border-radius:50%;background:var(--white);display:flex;align-items:center;justify-content:center}
.feat-name{margin-top:40px;font-family:"Montserrat",sans-serif;font-weight:500;font-size:19px;color:#222}
.feat-item.active{top:-13px;height:355px;background:var(--white);box-shadow:0 2px 10px rgba(0,0,0,.06)}
.feat-item.active .feat-thumb{margin-top:27px;width:194px;height:194px;background:var(--light)}
.feat-item.active .feat-name{margin-top:26px}
.feat-desc{margin-top:12px;font-family:"Montserrat",sans-serif;font-size:14px;line-height:22px;color:#666}
.feat-item .btn{margin-top:14px;width:151px;height:36px}
.bottle{width:60px;height:78px;border-radius:10px 10px 6px 6px}

/* story */
.section-title{position:absolute;font-family:"Nunito",sans-serif;font-weight:400;font-size:44px;color:var(--ink)}
.story-text{position:absolute;left:148px;width:904px;top:1207px;text-align:center;font-family:"Montserrat",sans-serif;font-size:14.6px;line-height:21.7px;color:var(--text)}
.story-text p+p{margin-top:21.7px}
.story .btn{position:absolute;left:524px;top:1413px;width:151px;height:36px}
.story-photo{position:absolute;top:1442px;left:0;width:1200px;height:234px;background:linear-gradient(180deg,#fff 0%,#d9d6d2 35%,#9ba3a8 70%,#4d5760 100%)}

/* products */
.product-card{position:absolute;width:311px;height:405px;background:var(--white);box-shadow:0 1px 8px rgba(0,0,0,.12);text-align:center}
.product-media{margin:11px 13px 0;height:263px;border-radius:29px;background:var(--card);display:flex;align-items:center;justify-content:center}
.product-name{margin-top:22px;font-family:"Nunito",sans-serif;font-size:22px;color:#222;letter-spacing:.3px;white-space:nowrap}
.btn-outline{display:inline-flex;align-items:center;justify-content:center;margin-top:14px;width:182px;height:42px;border:2px solid var(--blue-dark);border-radius:22px;font-size:14px;font-weight:700;color:var(--blue-dark)}

/* contact */
.contact{position:absolute;top:2749px;left:0;width:1200px;height:511px;background:linear-gradient(90deg,rgba(6,110,180,.97),var(--blue) 60%);border-radius:0 110px 0 0}
.contact .section-title{color:var(--white);top:68px}
.field{position:absolute;background:var(--white);display:flex;align-items:center;gap:8px;padding-left:26px;font-size:14px;color:#666}
.field.msg{align-items:flex-start;padding-top:26px}
.btn-submit{position:absolute;left:522px;top:391px;width:156px;height:41px;border-radius:21px;background:var(--navy);color:var(--white);font-size:14px;font-weight:700;display:flex;align-items:center;justify-content:center}

/* footer */
.site-footer{position:absolute;top:3260px;left:0;width:1200px;height:474px;background:var(--footer);color:var(--white)}
.footer-logo{position:absolute;top:80px;left:0;width:1200px;display:flex;justify-content:center;align-items:center;gap:10px;font-family:"Nunito",sans-serif;font-weight:300;font-size:30px;letter-spacing:1px}
.footer-logo .dot{width:13px;height:13px;border-radius:50%;background:var(--white)}
.footer-nav{position:absolute;top:158px;font-size:14px;font-weight:700}
.footer-nav span{margin:0 14px;font-weight:400}
.info{position:absolute;top:214px;width:320px;text-align:center}
.info-icon{margin:0 auto;width:55px;height:55px;border-radius:50%;background:var(--blue);display:flex;align-items:center;justify-content:center}
.info-label{margin-top:10px;font-family:"Nunito",sans-serif;font-size:19px;color:var(--blue)}
.info-value{margin-top:6px;font-family:"Nunito",sans-serif;font-weight:600;font-size:19px;line-height:24px}
.copyright{position:absolute;top:400px;font-size:14px}
</style>
</head>
<body>

<header class="site-header">
  <div class="logo"><span>ORBILINK</span><span class="dot"></span></div>
  <div class="call-badge">
    <svg width="14" height="18" viewBox="0 0 14 18"><rect x="2" y="1" width="10" height="16" rx="2" fill="none" stroke="#fff" stroke-width="2"/><circle cx="7" cy="14" r="1" fill="#fff"/></svg>
    Call Us Anytime : <b>+1 888 888 8888</b>
  </div>
  <nav class="main-nav">
    <a class="active" style="left:0">HOME</a>
    <a style="left:68px">ABOUT US</a>
    <a style="left:163px">OUR PRODUCTS</a>
    <a style="left:300px">BLOG</a>
    <a style="left:363px">CONTACT US</a>
  </nav>
</header>

<section class="hero">
  <div role="img" aria-label="Laboratory glassware with glowing blue and purple liquids" style="position:absolute;inset:0"></div>
  <div class="hero-panel"></div>
  <h1 class="hero-title center">ORBILINK</h1>
  <p class="hero-text center">Lorem ipsum dolor sit amet, consectetur adipiscing elit, sed do eiusmod tempor<br>incididunt ut labore et dolore magna aliqua.</p>
  <span class="btn">GET STARTED</span>
  <span class="hero-arrow" style="left:33px"><svg width="10" height="14"><path d="M7 2 2 7l5 5" fill="none" stroke="#333" stroke-width="1.6"/></svg></span>
  <span class="hero-arrow" style="left:1122px"><svg width="10" height="14"><path d="M3 2l5 5-5 5" fill="none" stroke="#333" stroke-width="1.6"/></svg></span>
  <div class="hero-dots"><span></span><span class="on"></span><span></span></div>
</section>

<section class="featured">
  <div class="feat-item" style="left:0">
    <div class="feat-thumb"><div class="bottle" role="img" aria-label="Yellow chemical container" style="background:linear-gradient(#f7d84a,#e9b820)"></div></div>
    <div class="feat-name">Nemo enim ipsam</div>
  </div>
  <div class="feat-item" style="left:239px">
    <div class="feat-thumb"><div class="bottle" role="img" aria-label="Yellow aerosol canister" style="width:28px;background:linear-gradient(#f2c94c,#d9a51f)"></div></div>
    <div class="feat-name">Nemo enim ipsam</div>
  </div>
  <div class="feat-item active" style="left:480px">
    <div class="feat-thumb"><div class="bottle" role="img" aria-label="Red chemical container" style="width:90px;height:110px;background:linear-gradient(#e8332c,#c51f1a)"></div></div>
    <div class="feat-name">Nemo enim ipsam</div>
    <div class="feat-desc">Lorem ipsum dolor sit<br>amet, consectetur</div>
    <span class="btn">READ MORE <svg width="14" height="14"><circle cx="7" cy="7" r="7" fill="#fff"/><path d="M6 4l3 3-3 3" fill="none" stroke="#0a8ad9" stroke-width="1.8"/></svg></span>
  </div>
  <div class="feat-item" style="left:719px">
    <div class="feat-thumb" style="width:164px;height:164px;margin-top:28px"><div class="bottle" role="img" aria-label="Blue chemical container" style="width:80px;height:100px;background:linear-gradient(#3a78d8,#1c56b3)"></div></div>
    <div class="feat-name" style="margin-top:28px">Nemo enim ipsam</div>
  </div>
  <div class="feat-item" style="left:960px">
    <div class="feat-thumb"><div class="bottle" role="img" aria-label="Light blue aerosol canister" style="width:28px;background:linear-gradient(#8fd4e8,#4bb0d0)"></div></div>
    <div class="feat-name">Nemo enim ipsam</div>
  </div>
</section>

<section class="story">
  <h2 class="section-title center" style="top:1146px">OUR STORY</h2>
  <div class="story-text">
    <p>Lorem ipsum dolor sit amet, consectetur adipiscing elit, sed do eiusmod tempor incididunt ut labore et dolore magna aliqua. Ut enim ad minim veniam, quis nostrud exercitation ullamco laboris nisi ut aliquip ex ea commodo consequat. Duis aute irure dolor in reprehenderit in voluptate velit esse cillum dolore eu fugiat nulla pariatur.</p>
    <p>Excepteur sint occaecat cupidatat non proident, sunt in culpa qui officia deserunt mollit anim id est laborum. Lorem ipsum dolor sit amet, consectetur adipiscing elit, sed do eiusmod tempor incididunt ut labore et dolore magna aliqua. Ut enim ad minim veniam, quis nostrud exercitation ullamco laboris nisi ut aliquip ex ea commodo consequat. Duis aute irure dolor in reprehenderit in voluptate velit esse cillum dolore eu fugiat nulla pariatur. Excepteur sint occaecat cupidatat non proident, sunt in culpa qui officia deserunt mollit anim id est laborum.</p>
  </div>
  <div class="story-photo" role="img" aria-label="Chemical refinery skyline at sunset"></div>
  <span class="btn">READ MORE <svg width="14" height="14"><circle cx="7" cy="7" r="7" fill="#fff"/><path d="M6 4l3 3-3 3" fill="none" stroke="#0a8ad9" stroke-width="1.8"/></svg></span>
</section>

<section class="products">
  <h2 class="section-title center" style="top:1749px">ALL PRODUCTS</h2>
  <div class="product-card" style="left:112px;top:1837px">
    <div class="product-media" role="img" aria-label="Black magnetic system filter"><div style="width:50px;height:110px;border-radius:14px;background:#2a2a2a"></div></div>
    <div class="product-name">CLARIFEX SWIRL™</div><span class="btn-outline">PRODUCT DETAILS</span>
  </div>
  <div class="product-card" style="left:444px;top:1837px">
    <div class="product-media" role="img" aria-label="Red power flushing unit"><div style="width:70px;height:170px;border-radius:30px 30px 10px 10px;background:#e2401f"></div></div>
    <div class="product-name">PURGELINE P75</div><span class="btn-outline">PRODUCT DETAILS</span>
  </div>
  <div class="product-card" style="left:777px;top:1837px">
    <div class="product-media" role="img" aria-label="Green test kit carry case"><div style="width:130px;height:100px;border-radius:8px;background:linear-gradient(#2e6fcf 0 12%,#3fa54a 12%)"></div></div>
    <div class="product-name">PURGELINE TEST KIT</div><span class="btn-outline">PRODUCT DETAILS</span>
  </div>
  <div class="product-card" style="left:112px;top:2262px">
    <div class="product-media" role="img" aria-label="White solar thermal fluid container"><div style="width:110px;height:150px;border-radius:10px;background:linear-gradient(#fff 0 25%,#d72a2a 25% 75%,#fff 75%)"></div></div>
    <div class="product-name">H10 SOLAR THERMAL</div><span class="btn-outline">PRODUCT DETAILS</span>
  </div>
  <div class="product-card" style="left:444px;top:2262px">
    <div class="product-media" role="img" aria-label="Two white solar cleaner containers"><div style="width:140px;height:100px;border-radius:10px;background:linear-gradient(90deg,#f6f6f6,#dcdcdc)"></div></div>
    <div class="product-name">H20 SOLAR CLEANER</div><span class="btn-outline">PRODUCT DETAILS</span>
  </div>
  <div class="product-card" style="left:777px;top:2262px">
    <div class="product-media" role="img" aria-label="Turquoise system cleaner container"><div style="width:95px;height:120px;border-radius:10px;background:linear-gradient(#7fe0da,#3ec3c1)"></div></div>
    <div class="product-name">KESTREL Q7 CLEANER</div><span class="btn-outline">PRODUCT DETAILS</span>
  </div>
</section>

<section class="contact" role="img" aria-label="Blue tinted city buildings background">
  <h2 class="section-title center">GET IN TOUCH</h2>
  <div class="field" style="left:112px;top:146px;width:315px;height:70px"><svg width="12" height="12"><circle cx="6" cy="3.5" r="3" fill="#0a8ad9"/><path d="M0 12a6 5 0 0 1 12 0z" fill="#0a8ad9"/></svg>Name</div>
  <div class="field" style="left:442px;top:146px;width:316px;height:70px"><svg width="13" height="10"><rect width="13" height="10" rx="1" fill="#0a8ad9"/><path d="M0 1l6.5 5L13 1" fill="none" stroke="#fff" stroke-width="1.2"/></svg>Email address</div>
  <div class="field" style="left:772px;top:146px;width:316px;height:70px"><svg width="12" height="12"><path d="M2 0h3l1 3-2 1.5a7 7 0 0 0 3.5 3.5L9 6l3 1v3a2 2 0 0 1-2 2A10 10 0 0 1 0 2a2 2 0 0 1 2-2z" fill="#0a8ad9"/></svg>Phone</div>
  <div class="field msg" style="left:112px;top:233px;width:976px;height:139px"><svg width="12" height="12"><path d="M0 12l1-4 7-7 3 3-7 7z" fill="#0a8ad9"/></svg>Message</div>
  <span class="btn-submit">SUBMIT NOW</span>
</section>

<footer class="site-footer">
  <div class="footer-logo"><span>ORBILINK</span><span class="dot"></span></div>
  <div class="footer-nav center">HOME<span>|</span>ABOUT US<span>|</span>OUR PRODUCTS<span>|</span>CONTACT US</div>
  <div class="info" style="left:102px">
    <div class="info-icon"><svg width="22" height="28" viewBox="0 0 22 28"><path d="M11 27S2 16 2 10a9 9 0 0 1 18 0c0 6-9 17-9 17z" fill="none" stroke="#fff" stroke-width="2"/><circle cx="11" cy="10" r="3.5" fill="none" stroke="#fff" stroke-width="2"/></svg></div>
    <div class="info-label">Address :</div>
    <div class="info-value">123,Lorem ipsum dolor sit<br>amet, consec</div>
  </div>
  <div class="info" style="left:427px">
    <div class="info-icon"><svg width="26" height="26" viewBox="0 0 26 26"><path d="M5 3h4l2 5-3 2a12 12 0 0 0 8 8l2-3 5 2v4a3 3 0 0 1-3 3A20 20 0 0 1 2 6a3 3 0 0 1 3-3z" fill="none" stroke="#fff" stroke-width="1.8"/></svg></div>
    <div class="info-label">Phone :</div>
    <div class="info-value">+1 888 888 8888</div>
  </div>
  <div class="info" style="left:759px">
    <div class="info-icon"><svg width="26" height="20" viewBox="0 0 26 20"><rect x="1" y="1" width="24" height="18" rx="2" fill="none" stroke="#fff" stroke-width="2"/><path d="M1 2l12 9 12-9M1 18l9-7M25 18l-9-7" fill="none" stroke="#fff" stroke-width="1.6"/></svg></div>
    <div class="info-label">Email address :</div>
    <div class="info-value">info@companyname.com</div>
  </div>
  <div class="copyright center">© Copyrights 2023 Company name | All Rights Reserved</div>
</footer>

</body>
</html>
```